Business Card Design - ChoiceCraft

Looking for creative, modern design, two sided for ChoiceCraft that is consistent with color and feel of website www.choicecraftpro.net.
Updates

Back of card will be used to promote products or have a quote revolving around decisions, change, leadership, innovation, creativity. Back should also have space to promote website, but optional to use the icon. Front of the card will need to use the icon and have standard place for name, job title, phone and email. We are not looking to put a mailing address or fax. Also want space to place a few words/phrase explaining what we do...such as individual growth and organizational development or tools, training, information...in addition, want the facebook icon small on the front somewhere as we are also on facebook.

Vector file uploaded of icon.

Target Market(s)

Professional coaching for individual growth and organizational development

Industry/Entity Type

Business

Requirements
Must have
• Icon...see attached.

```html
<!DOCTYPE html>
<html lang="en">
<head>
<meta charset="utf-8">
<title>ChoiceCraft – Business Card</title>
<link rel="stylesheet" href="https://fonts.googleapis.com/css2?family=Open+Sans:wght@400;600;700&family=Arimo:wght@400;700&display=swap">
<style>
  :root {
    --stage: #1c1c1c;
    --card: #ffffff;
    --blue: #0b72c0;
    --blue-light: #2bb8ec;
    --sky: #7cc6ef;
    --ink: #333333;
    --grey: #6b6b6b;
    --rule: #b9b9b9;
  }
  * { box-sizing: border-box; margin: 0; padding: 0; }
  html, body {
    width: 1200px; height: 761px; overflow: hidden;
    background: var(--stage);
  }
  .sheet { position: relative; width: 1200px; height: 761px; }

  .card {
    position: absolute; top: 215px;
    width: 560px; height: 330px;
    background: var(--card);
    border-radius: 22px;
    overflow: hidden;
  }
  .card--front { left: 25px; }
  .card--back { left: 615px; }

  /* front */
  .edge-band {
    position: absolute; top: 0; right: 0; width: 56px; height: 100%;
    background: linear-gradient(180deg, var(--blue) 0%, var(--blue-light) 100%);
    border-left: 4px solid #d6eefa;
  }
  .brand {
    position: absolute; left: 40px; top: 60px; width: 160px;
    display: flex; flex-direction: column; align-items: center; gap: 14px;
    font-family: "Open Sans", sans-serif;
  }
  .brand__dot {
    width: 96px; height: 96px; border-radius: 50%;
    background: radial-gradient(circle at 40% 40%, #e6f3fb 0%, var(--sky) 60%, var(--blue) 100%);
  }
  .brand__name { font-size: 17px; font-weight: 400; color: #1a1a1a; }
  .divider {
    position: absolute; left: 222px; top: 36px; width: 2px; height: 170px;
    background: linear-gradient(180deg, transparent, var(--rule) 30%, var(--rule) 70%, transparent);
  }
  .person {
    position: absolute; left: 242px; top: 40px;
    font-family: "Open Sans", sans-serif; color: var(--ink);
  }
  .person__name { font-size: 22px; font-weight: 700; color: var(--blue); line-height: 1.1; }
  .person__title { font-size: 15px; color: var(--grey); margin: 4px 0 12px; }
  .contact { list-style: none; font-size: 14px; line-height: 1.4; }
  .contact li { display: flex; align-items: center; gap: 6px; }
  .contact svg { width: 12px; height: 12px; flex: none; }
  .contact .square { width: 11px; height: 11px; background: var(--blue); border-radius: 2px; flex: none; }
  .tagline {
    position: absolute; left: 0; right: 56px; top: 245px;
    text-align: center; font-family: "Open Sans", sans-serif;
    font-size: 17px; line-height: 1.3; color: var(--grey);
  }

  /* back */
  .quotes {
    position: absolute; left: 34px; top: 26px; right: 30px;
    list-style: none; font-family: "Arimo", sans-serif;
  }
  .quote { margin-bottom: 9px; }
  .quote__text { font-size: 14.5px; color: var(--ink); line-height: 1.25; }
  .quote__text::before, .quote__text::after {
    font-family: Georgia, serif; font-weight: 700; font-size: 20px; color: var(--ink);
    line-height: 0; vertical-align: -4px;
  }
  .quote__text::before { content: "\201C"; margin-right: 3px; }
  .quote__text::after { content: "\201D"; margin-left: 2px; }
  .quote__by { font-size: 14.5px; font-weight: 700; color: var(--blue-light); margin-left: 18px; }
  .back-mark {
    position: absolute; right: 30px; bottom: 22px;
    display: flex; flex-direction: column; align-items: center; gap: 6px;
    font-family: "Open Sans", sans-serif; font-size: 14px; color: #1a1a1a;
  }
  .back-mark__dot {
    width: 90px; height: 90px; border-radius: 50%;
    background: radial-gradient(circle at 40% 40%, #eef6fb 0%, #bfe2f6 55%, var(--sky) 100%);
  }
</style>
</head>
<body>
<main class="sheet">

  <section class="card card--front" aria-label="Card front">
    <div class="brand">
      <span class="brand__dot"></span>
      <span class="brand__name">ChoiceCraft</span>
    </div>
    <span class="divider"></span>
    <div class="person">
      <p class="person__name">Your Name</p>
      <p class="person__title">Title</p>
      <ul class="contact">
        <li><svg viewBox="0 0 12 12"><circle cx="6" cy="6" r="5.2" fill="none" stroke="#333" stroke-width="1"/><path d="M4 3.2l1 1.2-.6.8c.4.9 1 1.5 1.9 1.9l.8-.6 1.2 1-.6 1c-2.3-.3-4-2-4.3-4.3z" fill="#333"/></svg>123-456-789</li>
        <li><svg viewBox="0 0 12 12"><rect x="1" y="2.5" width="10" height="7" rx="1" fill="#333"/><path d="M1.5 3l4.5 3.5L10.5 3" fill="none" stroke="#fff" stroke-width="1"/></svg>info@choicecraftpro.net</li>
        <li><svg viewBox="0 0 12 12"><circle cx="6" cy="6" r="5" fill="none" stroke="#333" stroke-width="1"/><ellipse cx="6" cy="6" rx="2.2" ry="5" fill="none" stroke="#333" stroke-width="0.9"/><path d="M1 6h10M2 3.5h8M2 8.5h8" stroke="#333" stroke-width="0.8"/></svg>www.choicecraftpro.net</li>
        <li><span class="square"></span>/choicecraftpro</li>
      </ul>
    </div>
    <p class="tagline">Supporting individual growth and organizational<br>development or tools, training, information</p>
    <span class="edge-band"></span>
  </section>

  <section class="card card--back" aria-label="Card back">
    <ul class="quotes">
      <li class="quote"><p class="quote__text">Try not to become a man of success, but rather a man of value.</p><p class="quote__by">- Arlen Whitcombe</p></li>
      <li class="quote"><p class="quote__text">The only constant is change.</p><p class="quote__by">- Helios Dorane</p></li>
      <li class="quote"><p class="quote__text">We are what we repeatedly do. Excellence is not an act, it is a habit.</p><p class="quote__by">- Aristen Moor</p></li>
      <li class="quote"><p class="quote__text">Simplicity is the ultimate sophistication.</p><p class="quote__by">- Lorenzo Vellani</p></li>
      <li class="quote"><p class="quote__text">Life is not fair - get used to it.</p><p class="quote__by">- Ben Galloway</p></li>
    </ul>
    <div class="back-mark">
      <span class="back-mark__dot"></span>
      <span>ChoiceCraft</span>
    </div>
  </section>

</main>
</body>
</html>
```